Classy, Elegant, Simple Business Card Design

Looking to have a classy, simple, and elegant design. Want a top notch designed business card. I really like the look of the new torvane credit card. I also like the design I attached. I am trying to reach 21-29 year old females for booking us for there wedding or event. We offer Disc Jockey Service, Photo Booth Rentals, and Uplighting .

Target Market(s)

21-28 year old females

Contact Information for Business Card

Has to have logo, website, email, and phone number

Font styles to use
Other font styles liked:
• open to font choice, modern, clean
Designer to choose
33a6d7
0791cd
0555a3
ffffff

Requirements
Must have
• Has to have logo, website, email, and phone number
Nice to have
• I really like the design of the new torvane credit card. I also included my logo and some designs I like
Should not have
• clutter or too much info

```html
<!DOCTYPE html>
<html lang="en">
<head>
<meta charset="utf-8">
<title>Tidewell Event Group – Business Card</title>
<link href="https://fonts.googleapis.com/css2?family=Lato:wght@400;700&display=swap" rel="stylesheet">
<style>
  :root {
    --backdrop: #8c8c8c;
    --card: #ffffff;
    --card-back: #f7f7f7;
    --ink: #1c2f5a;
    --blue-light: #33a6d7;
    --blue: #0791cd;
    --blue-deep: #0555a3;
  }
  * { margin: 0; padding: 0; box-sizing: border-box; }
  html, body {
    width: 1200px; height: 802px; overflow: hidden;
    background: var(--backdrop);
    font-family: "Lato", sans-serif;
  }
  .canvas { position: relative; width: 1200px; height: 802px; }
  .card {
    position: absolute; top: 274px;
    width: 436px; height: 265px;
    border-radius: 16px; overflow: hidden;
    box-shadow: 2px 3px 6px rgba(0,0,0,0.35);
  }
  .card--front { left: 136px; background: var(--card); }
  .card--back { left: 626px; background: var(--card-back); }

  .monogram-area {
    position: absolute; inset: 0;
    width: 436px; height: 265px;
  }

  .contact-list {
    position: absolute; left: 20px; top: 60px;
    list-style: none; color: var(--ink);
    font-size: 14.5px; line-height: 19.5px;
  }
  .contact-list li { display: flex; align-items: center; gap: 3px; }
  .contact-list svg { width: 16px; height: 16px; flex: none; }

  .service-list {
    position: absolute; left: 23px; top: 145px;
    list-style: none; color: var(--ink);
    font-size: 14.5px; line-height: 19.5px;
  }
  .service-list li { display: flex; align-items: center; gap: 6px; }
  .service-list li::before {
    content: ""; width: 7px; height: 7px; border-radius: 50%;
    background: var(--blue);
  }

  .brand {
    position: absolute; left: 0; right: 0; top: 96px;
    display: flex; flex-direction: column; align-items: center; gap: 12px;
  }
  .brand__dot { width: 26px; height: 26px; border-radius: 50%; background: var(--blue); }
  .brand__name {
    font-size: 24px; font-weight: 400; color: var(--blue-deep);
    letter-spacing: 1px;
  }
</style>
</head>
<body>
<main class="canvas">
  <section class="card card--front">
    <svg class="monogram-area" viewBox="0 0 436 265" role="img" aria-label="Large decorative blue script monogram">
      <defs>
        <linearGradient id="monogramTone" x1="0" y1="0" x2="1" y2="1">
          <stop offset="0" stop-color="var(--blue-light)"/>
          <stop offset="0.55" stop-color="var(--blue)"/>
          <stop offset="1" stop-color="var(--blue-deep)"/>
        </linearGradient>
      </defs>
      <path d="M300 0 L436 0 L436 265 L215 265 C170 255 160 220 175 195 C190 170 230 150 260 140 C300 125 300 100 290 70 C280 40 285 10 300 0 Z" fill="url(#monogramTone)"/>
    </svg>

    <ul class="contact-list">
      <li>
        <svg viewBox="0 0 16 16" aria-hidden="true"><circle cx="8" cy="8" r="8" fill="var(--ink)"/><path d="M4 6.5c0-1.2 1.8-2 4-2s4 .8 4 2l-1.3.6-.6-1H6l-.6 1zM5.2 8h5.6l.8 3.5H4.4z" fill="#fff"/></svg>
        055-246 813 579
      </li>
      <li>
        <svg viewBox="0 0 16 16" aria-hidden="true"><circle cx="8" cy="8" r="8" fill="var(--ink)"/><rect x="4" y="5.2" width="8" height="5.6" fill="#fff"/><path d="M4 5.2l4 3 4-3" fill="none" stroke="var(--ink)" stroke-width="0.9"/></svg>
        hello@tidewellevents.com
      </li>
      <li>
        <svg viewBox="0 0 16 16" aria-hidden="true"><circle cx="8" cy="8" r="8" fill="var(--ink)"/><circle cx="8" cy="8" r="4" fill="#fff"/><path d="M4 8h8M8 4c-1.5 1.5-1.5 6.5 0 8M8 4c1.5 1.5 1.5 6.5 0 8" fill="none" stroke="var(--ink)" stroke-width="0.8"/></svg>
        www.tidewellevents.com
      </li>
    </ul>

    <ul class="service-list">
      <li>Disc Jockey Service</li>
      <li>Photo Booth Rentals</li>
      <li>Uplighting</li>
    </ul>
  </section>

  <section class="card card--back">
    <div class="brand">
      <span class="brand__dot" aria-hidden="true"></span>
      <span class="brand__name">Tidewell Event Group</span>
    </div>
  </section>
</main>
</body>
</html>
```